Private Investment Firm Needs PowerPoint Presentation Template

Design PowerPoint template, take Pinebrook-submitted rough presentation draft, and drop it into new template. See attached Project Brief file for more detail.
Updates

Some decent designs have been submitted but they seem to lack the understanding of our target markets. I am hopeful that more time and feedback will result in better results.

Target Market(s)

Private company owners and intermediaries.

Font styles to use
Serif

Colors
3176b5

Requirements
Must have
• See attached Project Brief.
Nice to have
Should not have
• No B2C fluff--this is a B2B project.

```html
<!DOCTYPE html>
<html lang="en">
<head>
<meta charset="utf-8">
<title>Investment Criteria – Pinebrook</title>
<link href="https://fonts.googleapis.com/css2?family=Montserrat:wght@400;500;600;700&family=Libre+Baskerville:wght@400&display=swap" rel="stylesheet">
<style>
  :root {
    --brand-blue: #0b66c2;
    --panel-blue: #0a62b5;
    --photo-dark: #0f3a4a;
    --photo-mid: #1f5f6c;
    --ink-grey: #555759;
    --white: #ffffff;
  }
  * { margin: 0; padding: 0; box-sizing: border-box; }
  html, body { width: 1200px; height: 676px; overflow: hidden; background: var(--white); }
  .slide {
    position: relative;
    width: 1200px; height: 676px;
    background: var(--white);
    font-family: "Montserrat", sans-serif;
    overflow: hidden;
  }
  .side-rail {
    position: absolute; left: 0; top: 0;
    width: 44px; height: 676px;
    background: var(--brand-blue);
  }
  .side-rail__url {
    position: absolute;
    left: 22px; top: 336px;
    transform: translate(-50%, -50%) rotate(-90deg);
    font-family: "Libre Baskerville", serif;
    font-size: 13px;
    color: var(--white);
    white-space: nowrap;
  }
  .edge-rail {
    position: absolute; right: 0; top: 0;
    width: 12px; height: 676px;
    background: var(--brand-blue);
  }
  .page-number {
    position: absolute; right: 22px; top: 19px;
    font-family: "Libre Baskerville", serif;
    font-size: 17px;
    color: #222;
  }
  .section-title {
    position: absolute; left: 86px; top: 82px;
    font-size: 28.6px; font-weight: 600;
    letter-spacing: 0.3px;
    color: var(--brand-blue);
  }
  .headline {
    position: absolute; right: 749px; top: 226px;
    text-align: right;
    font-size: 40px; font-weight: 600;
    line-height: 42px;
    color: var(--ink-grey);
  }
  .headline__accent { color: var(--brand-blue); }
  .photo-band {
    position: absolute; left: 483px; top: 101px;
    width: 705px; height: 470px;
    background: linear-gradient(135deg, var(--photo-dark) 0%, var(--photo-mid) 45%, var(--photo-dark) 100%);
  }
  .criteria-panel {
    position: absolute; left: 483px; top: 170px;
    width: 705px; height: 334px;
    background: var(--panel-blue);
    padding: 33px 0 0 36px;
  }
  .criteria-list { list-style: none; }
  .criteria-list li {
    display: flex; align-items: center;
    height: 37.6px;
    font-size: 17.4px; font-weight: 500;
    color: var(--white);
    white-space: nowrap;
  }
  .criteria-list svg { width: 14px; height: 14px; margin-right: 11px; flex: none; }
  .brand {
    position: absolute; left: 67px; top: 612px;
    display: flex; align-items: center;
  }
  .brand__mark {
    width: 36px; height: 36px; border-radius: 50%;
    background: var(--brand-blue);
    margin-right: 10px;
  }
  .brand__name {
    font-size: 17px; font-weight: 600; letter-spacing: 1.6px;
    color: var(--brand-blue); line-height: 1.1;
  }
  .brand__tagline {
    font-size: 6.6px; font-weight: 600; letter-spacing: 0.5px;
    color: var(--brand-blue); margin-top: 4px;
  }
</style>
</head>
<body>
<div class="slide">
  <div class="side-rail"><span class="side-rail__url">www.pinebrookfund.example</span></div>
  <div class="edge-rail"></div>
  <div class="page-number">12</div>

  <h1 class="section-title">INVESTMENT CRITERIA</h1>

  <p class="headline"><span class="headline__accent">Pinebrook invests</span><br>in established,<br>lower middle<br>market<br>companies.</p>

  <div class="photo-band" role="img" aria-label="Photograph of scattered banknotes in a dark teal tint"></div>

  <div class="criteria-panel">
    <ul class="criteria-list">
      <li><svg viewBox="0 0 14 14"><path d="M7 1.5 L12.5 7 L7 12.5 L1.5 7 Z" fill="none" stroke="#fff" stroke-width="3"/></svg>Revenues of $10MM to $150MM</li>
      <li><svg viewBox="0 0 14 14"><path d="M7 1.5 L12.5 7 L7 12.5 L1.5 7 Z" fill="none" stroke="#fff" stroke-width="3"/></svg>EBITDA of at least $2MM</li>
      <li><svg viewBox="0 0 14 14"><path d="M7 1.5 L12.5 7 L7 12.5 L1.5 7 Z" fill="none" stroke="#fff" stroke-width="3"/></svg>Pinebrook investment size of $5MM to $25MM</li>
      <li><svg viewBox="0 0 14 14"><path d="M7 1.5 L12.5 7 L7 12.5 L1.5 7 Z" fill="none" stroke="#fff" stroke-width="3"/></svg>Experienced, committed, and incented management</li>
      <li><svg viewBox="0 0 14 14"><path d="M7 1.5 L12.5 7 L7 12.5 L1.5 7 Z" fill="none" stroke="#fff" stroke-width="3"/></svg>Limited leverage (aka debt) “ahead” of Pinebrook</li>
      <li><svg viewBox="0 0 14 14"><path d="M7 1.5 L12.5 7 L7 12.5 L1.5 7 Z" fill="none" stroke="#fff" stroke-width="3"/></svg>Niche market leader with differentiated services or products</li>
      <li><svg viewBox="0 0 14 14"><path d="M7 1.5 L12.5 7 L7 12.5 L1.5 7 Z" fill="none" stroke="#fff" stroke-width="3"/></svg>Focused on value-added execution, not proof of concept</li>
    </ul>
  </div>

  <div class="brand">
    <div class="brand__mark"></div>
    <div>
      <div class="brand__name">PINEBROOK</div>
      <div class="brand__tagline">MINORITY GROWTH INVESTMENT</div>
    </div>
  </div>
</div>
</body>
</html>
```